New Business Card Design Project

Use the flyer uploaded and website www.brightoakbuilders.com for inspiration.
List Our Services on Backside of business cards
Marcus Delling
Harborline Builders Inc.
Licensed General Contractors
858-471-6093

Contact Information for Business Card

Use the flyer uploaded and website www.brightoakbuilders.com for inspiration. List Our Services on Backside of business cards Marcus Delling Harborline Builders Inc. Licensed General Contractors 858-471-6093

```html
<!DOCTYPE html>
<html lang="en">
<head>
<meta charset="utf-8">
<title>Harborline Builders – Business Cards</title>
<link href="https://fonts.googleapis.com/css2?family=Montserrat:wght@400;500&family=Oswald:wght@600&display=swap" rel="stylesheet">
<style>
  :root {
    --backdrop: #2d2d2d;
    --card-black: #131313;
    --card-white: #ffffff;
    --accent-blue: #3784c8;
    --accent-red: #e3141d;
    --ink: #1b1b1b;
  }
  * { margin: 0; padding: 0; box-sizing: border-box; }
  html, body { width: 1200px; height: 1015px; overflow: hidden; }
  body {
    background: var(--backdrop);
    font-family: "Montserrat", sans-serif;
    color: var(--ink);
    position: relative;
  }
  .card {
    position: absolute;
    left: 215px;
    width: 770px;
    height: 440px;
    overflow: hidden;
    background: var(--card-white);
    box-shadow: 0 10px 24px rgba(0,0,0,.45);
  }
  .card--services { top: 47px; }
  .card--contact { top: 527px; }
  .card__shapes { position: absolute; inset: 0; width: 100%; height: 100%; }

  .brand {
    position: absolute;
    right: 48px;
    top: 62px;
    color: var(--card-white);
    font-family: "Montserrat", sans-serif;
    font-weight: 400;
    font-size: 24px;
    letter-spacing: 3px;
    white-space: nowrap;
  }

  .guarantee {
    position: absolute;
    left: 38px;
    top: 250px;
    font-family: "Oswald", sans-serif;
    font-weight: 600;
    font-size: 22px;
    line-height: 1.3;
    color: var(--accent-red);
    white-space: nowrap;
  }
  .specializing {
    position: absolute;
    left: 38px;
    top: 284px;
    background: var(--accent-blue);
    color: var(--card-white);
    font-family: "Oswald", sans-serif;
    font-weight: 600;
    font-size: 19px;
    line-height: 1.3;
    padding: 2px 14px;
  }
  .service-list {
    position: absolute;
    list-style: none;
    font-size: 16px;
    line-height: 1.35;
    color: var(--ink);
    white-space: nowrap;
  }
  .service-list li::before {
    content: "";
    display: inline-block;
    width: 7px; height: 7px;
    border-radius: 50%;
    background: var(--accent-blue);
    margin-right: 12px;
    vertical-align: middle;
  }
  .service-list--main { left: 40px; top: 324px; }
  .service-list--extra { left: 445px; top: 196px; }

  .person {
    position: absolute;
    left: 60px;
    top: 232px;
    font-family: "Oswald", sans-serif;
    font-weight: 600;
    font-size: 56px;
    color: var(--accent-red);
    letter-spacing: .5px;
    white-space: nowrap;
  }
  .contact-list {
    position: absolute;
    left: 62px;
    top: 320px;
    list-style: none;
    font-size: 19px;
    line-height: 1.6;
  }
  .contact-list li { display: flex; align-items: center; gap: 14px; }
  .contact-list svg { width: 20px; height: 20px; flex: none; }
  .company {
    position: absolute;
    right: 40px;
    top: 178px;
    text-align: right;
    color: var(--accent-red);
    font-weight: 500;
    font-size: 20px;
    line-height: 1.35;
  }
</style>
</head>
<body>

<section class="card card--services" aria-label="Services side">
  <svg class="card__shapes" viewBox="0 0 770 440" preserveAspectRatio="none" aria-hidden="true">
    <rect width="770" height="440" fill="var(--card-black)"/>
    <polygon points="0,250 240,198 770,110 770,440 0,440" fill="var(--card-white)"/>
    <polygon points="0,190 240,198 0,250" fill="var(--accent-blue)"/>
  </svg>
  <div class="brand">HARBORLINE BUILDERS</div>
  <div class="guarantee">OUR SERVICES ARE 100% GUARANTEED</div>
  <div class="specializing">SPECIALIZING IN</div>
  <ul class="service-list service-list--main">
    <li>Remodel: Kitchen &amp; Bath</li>
    <li>Painting: Interior &amp; Exterior</li>
    <li>Flooring: Carpet, Vinyl, Wood</li>
    <li>Window &amp; Door Replacement</li>
    <li>Plumbing: Repairs &amp; Upgrades</li>
  </ul>
  <ul class="service-list service-list--extra">
    <li>Energy-Efficient Upgrades</li>
    <li>Deck &amp; Patio Construction</li>
    <li>Water &amp; Mold Damage</li>
    <li>Garage Renovation</li>
  </ul>
</section>

<section class="card card--contact" aria-label="Contact side">
  <svg class="card__shapes" viewBox="0 0 770 440" preserveAspectRatio="none" aria-hidden="true">
    <rect width="770" height="440" fill="var(--card-black)"/>
    <polygon points="0,250 240,198 770,110 770,440 0,440" fill="var(--card-white)"/>
    <polygon points="0,190 240,198 0,250" fill="var(--accent-blue)"/>
  </svg>
  <div class="brand">HARBORLINE BUILDERS</div>
  <div class="company">Harborline Builders Inc.<br>Licensed General Contractors</div>
  <div class="person">MARCUS DELLING</div>
  <ul class="contact-list">
    <li>
      <svg viewBox="0 0 24 24" aria-hidden="true"><path fill="var(--accent-blue)" d="M6.6 10.8a15.1 15.1 0 0 0 6.6 6.6l2.2-2.2a1 1 0 0 1 1-.25 11.4 11.4 0 0 0 3.6.57 1 1 0 0 1 1 1V20a1 1 0 0 1-1 1A17 17 0 0 1 3 4a1 1 0 0 1 1-1h3.5a1 1 0 0 1 1 1c0 1.250.2 2.450.57 3.57a1 1 0 0 1-.25 1z"/></svg>
      858-471-6093
    </li>
    <li>
      <svg viewBox="0 0 24 24" aria-hidden="true"><rect x="2" y="5" width="20" height="14" fill="var(--accent-blue)"/><path d="M2 5l10 8 10-8" fill="none" stroke="#fff" stroke-width="1.6"/></svg>
      info@harborlinebuilders.com
    </li>
    <li>
      <svg viewBox="0 0 24 24" aria-hidden="true"><g fill="none" stroke="var(--accent-blue)" stroke-width="1.8"><circle cx="12" cy="12" r="9"/><ellipse cx="12" cy="12" rx="4" ry="9"/><path d="M3 12h18M5 7h14M5 17h14"/></g></svg>
      www.brightoakbuilders.com
    </li>
  </ul>
</section>

</body>
</html>
```